Thornbury Spa

We are a large Miami Beach spa and salon. I am still building our website but you can use it as a resource to gain a better understanding of who we are ....www.velloraspa-studio.com.

We offer a comprehensive list of services in hair, nails, massage, skin care, tanning, spray tanning and waxing and we offer high quality products for skin care, tanning and hair. We are open 7 days.

We would like to see a clean and simple menu that looks a lot like the one from "The Spa at Larkwood." In particular, we have a copy of a menu from their West Hollywood, CA location that is just beautiful. In the uploaded content you will see a sampling of that menu. We would like to see greys, blacks, silvers, whites and warm colors like reds and oranges. We specifically attempt to remain gender neutral so that we don't attract only girls (with pink colors and flowers etc). The final design should convey a simple, clean, friendly environment and the final product should be sized such that it is 1.) portable and 2.) inexpensive to print. We will be running thousands of these at a time so cost of printing is a consideration.

The booklet consists of two parts: one part is the standard menu with descriptions of services and products and photos etc (think of this as the sales piece that convinces a potential customer to visit) and will be stapled together like you would expect a small menu to be and should resemble the Larkwood menu. The prices should not be included in this part of the booklet that will be printed and stapled. The other part is a single insert and is removable and replaceable. I want this removable insert placed in the last page of the book in a folder pocket or something else that you can think of so that when it's time to change prices here that I am not throwing away all of the booklets....I am only replacing the inserts at the end of the menu booklet. Please design this single page insert so that should a customer remove it from the booklet and keep it, that it stands alone with our name, logo, website and phone number. This page can and probably will have to be 2 sided.

At the back of the booklet, I also want the polices to be printed in one page (think fine print in any sort of business dealing.)

With regard to the look and feel slider of economical v upmarket...we definitely want to convey we deliver upmarket services at reasonable prices. Think, world class services and products at reasonable, everyday prices.

With regard to the uploaded files:
I uploaded both EPS and TIF formats. The colors in those files are not the palette we want at all. The colors we want use for the circular logo must match the standard colors as depicted in the uploaded file "Thornburytanrooms"

Target Market(s)

The target market is the average 20-35 year old in Miami Beach that cares about their appearance. The range of clientele is quite diverse.

Industry/Entity Type

Environment

Requirements
Must have
• It must have elegant and simple photographs that relate to the services being offered. We are selling a service set and an environment...so this menu should be reflect that goal. The logo should be repeated often throughout the book but in subtle ways.

Stock photos are fine as long as they don't seem obviously stock.

Should not have
• Nothing buddha like. Nothing themed. It should be all inclusive and not seek to identify with any particular group or gender.

Nothing that fits the stereotype of "Miami Beach." We want to represent ourselves in the same category as the best spas in the world because we moving everything we do in that direction. Think class!

```html
<!DOCTYPE html>
<html lang="en">
<head>
<meta charset="utf-8">
<title>Thornbury Spa – Threading &amp; Waxing</title>
<link rel="stylesheet" href="https://fonts.googleapis.com/css2?family=Source+Sans+3:wght@300;400;600&family=Cormorant+Garamond:wght@500&display=swap">
<style>
  :root {
    --paper: #ffffff;
    --trim: #8a8a8a;
    --copper: #c26a2a;
    --copper-light: #c9773a;
    --copper-deep: #7b4a24;
    --copper-dark: #5e3a1d;
    --ink-light: #ffffff;
    --title-ink: #55575c;
    --band: rgba(255, 255, 255, 0.72);
    --frame: rgba(255, 255, 255, 0.85);
    --logo-tone: #e6d9c6;
  }
  * { box-sizing: border-box; margin: 0; padding: 0; }
  html, body {
    width: 1200px; height: 600px; overflow: hidden;
    background: var(--paper);
    font-family: "Source Sans 3", "Myriad Pro", Arial, sans-serif;
  }
  .canvas { position: relative; width: 1200px; height: 600px; }

  .crop-mark {
    position: absolute; left: 600px; width: 1px; background: var(--trim);
  }
  .crop-mark--top { top: 4px; height: 23px; }
  .crop-mark--bottom { top: 572px; height: 24px; }

  .spread {
    position: absolute; left: 65px; top: 30px;
    width: 1072px; height: 533px; overflow: hidden;
  }
  .spread__copper {
    position: absolute; left: 520px; top: 0; right: 0; bottom: 0;
    background:
      radial-gradient(ellipse 60% 55% at 78% 60%, rgba(255,200,140,0.18), transparent 70%),
      linear-gradient(135deg, var(--copper) 0%, var(--copper-light) 38%, var(--copper-deep) 78%, var(--copper-dark) 100%);
  }
  .spread__photo {
    position: absolute; left: 0; top: 0; width: 593px; height: 533px;
    border-bottom-right-radius: 150px 190px;
    background:
      radial-gradient(ellipse 30% 22% at 48% 10%, #f2efec 0%, transparent 70%),
      radial-gradient(ellipse 45% 35% at 78% 50%, #e8c0a6 0%, transparent 70%),
      radial-gradient(ellipse 28% 30% at 28% 55%, #c98f74 0%, transparent 70%),
      radial-gradient(ellipse 30% 25% at 10% 75%, #e9e6e2 0%, transparent 70%),
      linear-gradient(160deg, #3a3532 0%, #b98a72 35%, #d9ad92 60%, #7c6a60 100%);
  }
  .spread__frame {
    position: absolute; left: 17px; top: 15px; right: 15px; bottom: 16px;
    border: 1px solid var(--frame); pointer-events: none;
  }

  .cover-band {
    position: absolute; left: 0; top: 381px; width: 590px; height: 94px;
    background: var(--band);
  }
  .cover-title {
    position: absolute; left: 42px; top: 408px;
    font-weight: 300; font-size: 41px; letter-spacing: 0.5px;
    color: var(--title-ink); line-height: 1;
  }

  .menu {
    position: absolute; left: 628px; top: 63px; width: 400px;
    color: var(--ink-light);
  }
  .menu__header {
    display: flex; font-size: 10.5px; margin-bottom: 15px;
  }
  .menu__header-title { width: 233px; }
  .menu__header-col { width: 68px; }
  .menu__section-title { font-size: 8px; line-height: 11px; font-weight: 400; }
  .menu__section-title--large { font-size: 10px; line-height: 12px; }
  .menu__desc {
    font-size: 7.9px; line-height: 11px; margin-bottom: 11px;
  }
  .price-list { border-collapse: collapse; font-size: 7.9px; line-height: 11px; }
  .price-list td { padding: 0; white-space: nowrap; }
  .price-list .item { width: 198px; }
  .price-list .resident { width: 75px; text-align: right; }
  .price-list .guest { width: 68px; text-align: right; }
  .price-list--threading { margin-bottom: 22px; }

  .brand {
    position: absolute; left: 917px; top: 462px; width: 120px;
    text-align: center; color: var(--logo-tone);
    font-family: "Cormorant Garamond", Georgia, serif; font-weight: 500;
  }
  .brand__mark {
    width: 24px; height: 24px; border-radius: 50%;
    border: 1px solid var(--logo-tone); margin: 0 auto 3px;
  }
  .brand__name {
    font-size: 14px; line-height: 15px; letter-spacing: 0.5px; white-space: nowrap;
  }
</style>
</head>
<body>
<div class="canvas">
  <span class="crop-mark crop-mark--top"></span>
  <span class="crop-mark crop-mark--bottom"></span>

  <section class="spread">
    <div class="spread__copper"></div>
    <div class="spread__photo" role="img" aria-label="Photo of a client relaxing on a white towel while a therapist applies a waxing strip to his chest"></div>

    <div class="cover-band"></div>
    <h1 class="cover-title">THREADING &amp; WAXING</h1>

    <div class="menu">
      <div class="menu__header">
        <span class="menu__header-title">THREADING &amp; WAXING</span>
        <span class="menu__header-col">Residents</span>
        <span class="menu__header-col">Hotel Guests</span>
      </div>

      <h2 class="menu__section-title">THREADING</h2>
      <p class="menu__desc">Threading is an ancient hair removal technique passed down through the generations in Middle and Far Eastern countries. The technique utilizes only a single cotton thread, masterfully manipulated in the hands of our trained staff, to remove the entire hair follicle from areas of the face. Threading only removes the unwanted hair, without removing the top layer of skin, which is common to traditional waxing. The results can last up to six weeks depending on your hair's rate of regrowth, and because it uses only a disposable thread, it is perfectly sanitary and entirely chemical-free.</p>
      <table class="price-list price-list--threading">
        <tr><td class="item">Eyebrow</td><td class="resident">$15.00</td><td class="guest">$17.00</td></tr>
        <tr><td class="item">Upper Lip</td><td class="resident">$10.00</td><td class="guest">$12.00</td></tr>
        <tr><td class="item">Facial</td><td class="resident">from $25.00</td><td class="guest">from $30.00</td></tr>
      </table>

      <h2 class="menu__section-title menu__section-title--large">WAXING</h2>
      <p class="menu__desc">Waxing is perhaps the most commonly elected hair removal technique, where thin layers of warm wax are applied to the areas of unwanted hair, allowed to cool encapsulating the hair and the hair is then removed. Unlike threading which is restricted to facial areas, any area of the body can be waxed.</p>
      <table class="price-list price-list--waxing">
        <tr><td class="item">Eyebrows</td><td class="resident">$15.00</td><td class="guest">$18.00</td></tr>
        <tr><td class="item">Upper Lip</td><td class="resident">$ 8.00</td><td class="guest">$10.00</td></tr>
        <tr><td class="item">Nose</td><td class="resident">$ 8.00</td><td class="guest">$10.00</td></tr>
        <tr><td class="item">Chin</td><td class="resident">$ 8.00</td><td class="guest">$10.00</td></tr>
        <tr><td class="item">Chest</td><td class="resident">from $20.00</td><td class="guest">from $24.00</td></tr>
        <tr><td class="item">Stomach</td><td class="resident">from $17.00</td><td class="guest">from $20.00</td></tr>
        <tr><td class="item">Back</td><td class="resident">from $40.00</td><td class="guest">from $45.00</td></tr>
        <tr><td class="item">Underarm</td><td class="resident">$15.00</td><td class="guest">$18.00</td></tr>
        <tr><td class="item">Deep Bikini</td><td class="resident">$25.00</td><td class="guest">$30.00</td></tr>
        <tr><td class="item">Partial Brazilian</td><td class="resident">$35.00</td><td class="guest">$40.00</td></tr>
        <tr><td class="item">Full Brazilian</td><td class="resident">$45.00</td><td class="guest">$50.00</td></tr>
        <tr><td class="item">Buttocks (Female)</td><td class="resident">$10.00</td><td class="guest">$10.00</td></tr>
        <tr><td class="item">Buttocks (Male)</td><td class="resident">from $25.00</td><td class="guest">from $29.00</td></tr>
        <tr><td class="item">Half Arm</td><td class="resident">$15.00</td><td class="guest">$18.00</td></tr>
        <tr><td class="item">Full Arm</td><td class="resident">$22.00</td><td class="guest">$26.00</td></tr>
        <tr><td class="item">Half Leg</td><td class="resident">from $25.00</td><td class="guest">from $30.00</td></tr>
        <tr><td class="item">Full Leg</td><td class="resident">from $35.00</td><td class="guest">from $40.00</td></tr>
      </table>
    </div>

    <div class="brand">
      <div class="brand__mark"></div>
      <div class="brand__name">Thornbury Spa</div>
    </div>

    <div class="spread__frame"></div>
  </section>
</div>
</body>
</html>
```